Flyer for the Radiant Harvest Worship Day

I am looking to create a flyer for a one day prayer retreat our church is organizing.
This flyer will be posted on social media, websites and will also be printed so it can be mailed to people.
I am looking for something professional, with good use of our logo and band colors (logo colors).
I am counting on the designer's skill, creativity, art and knowledge of media communication to produce a flyer that will effectively and quickly convey the message we are trying to spread.
CONTENT OF THE FLYER:
Event title: Radiant Harvest Worship Day
Date: Tuesday July 2nd, 2019
Time: 11:00AM - 7:00PM
Belmora Hotel, 4875 Wexley Avenue, Portland, Maine 04102 (Room: Juniper)
Event Key words to highlight what the event is about: Prayer, Sharing the Word, Panel discussion, prophecy, Impartation.
Key phrases:
A one day prayer retreat.
Jesus Chris is Lord
Contact info:
www.tolvex.org
Phone: 207 555 3184
Email: contact@brookhavenfold.org

```html
<!DOCTYPE html>
<html lang="en">
<head>
<meta charset="utf-8">
<title>Radiant Harvest Worship Day</title>
<link href="https://fonts.googleapis.com/css2?family=Oswald:wght@500;600&family=Arimo:wght@400;700&display=swap" rel="stylesheet">
<style>
  :root {
    --navy: #0d3558;
    --orange: #f39a1f;
    --ink: #1f2b3a;
    --white: #ffffff;
    --rule: #8a9bb0;
    --frame: #9a9a9a;
  }
  * { margin: 0; padding: 0; box-sizing: border-box; }
  html, body { width: 866px; height: 1200px; overflow: hidden; background: var(--white); }
  .canvas {
    position: relative; width: 866px; height: 1200px;
    border: 1px solid var(--frame); background: var(--white);
    font-family: "Arimo", Arial, sans-serif;
  }
  .flyer { position: absolute; left: 42px; top: 47px; width: 781px; height: 1105px; background: var(--navy); overflow: hidden; }
  .top-band { position: absolute; left: 0; top: 0; width: 100%; height: 33px; background: var(--navy); }
  .hero-photo {
    position: absolute; left: 0; top: 33px; width: 100%; height: 541px;
    background:
      radial-gradient(ellipse 140px 220px at 640px 250px, #6a4a3a 0%, rgba(60,40,35,0) 100%),
      radial-gradient(ellipse 120px 200px at 430px 230px, #5a3d30 0%, rgba(60,40,35,0) 100%),
      radial-gradient(ellipse 110px 180px at 250px 200px, #b79c8c 0%, rgba(180,150,140,0) 100%),
      linear-gradient(90deg, #cfc7c8 0%, #b9adab 40%, #3b2f30 65%, #2a2224 100%);
  }
  .event-title {
    position: absolute; left: 53px; top: 250px; color: var(--white);
    font-family: "Oswald", "Arial Narrow", sans-serif; font-weight: 500; line-height: 1;
    text-transform: uppercase;
  }
  .event-title .line-one { display: block; font-size: 44px; letter-spacing: 0.2px; }
  .event-title .line-two { display: block; font-size: 64px; margin-top: 4px; }
  .logo-box {
    position: absolute; left: 555px; top: 390px; width: 185px; height: 184px;
    background: var(--navy); display: flex; align-items: center; justify-content: center;
  }
  .org-name { font-family: "Oswald", "Arial Narrow", sans-serif; font-weight: 500; color: var(--white); font-size: 42px; letter-spacing: 1px; }
  .retreat-band {
    position: absolute; left: 0; top: 580px; width: 100%; height: 115px;
    background: var(--orange); text-align: center;
  }
  .retreat-band .headline {
    font-family: "Oswald", "Arial Narrow", sans-serif; font-weight: 500;
    color: var(--white); font-size: 62px; line-height: 1; padding-top: 4px; text-transform: uppercase;
  }
  .retreat-band .tagline { font-weight: 700; color: var(--ink); font-size: 25px; margin-top: 5px; text-transform: uppercase; }
  .keywords { position: absolute; left: 0; top: 713px; width: 100%; text-align: center; color: var(--white); font-weight: 700; font-size: 30px; line-height: 40px; }
  .details { position: absolute; left: 0; top: 822px; width: 100%; height: 145px; }
  .detail { position: absolute; top: 0; color: var(--white); font-size: 24px; line-height: 36px; }
  .detail .icon { position: absolute; top: 2px; width: 32px; height: 32px; }
  .detail-date { left: 64px; }
  .detail-date .icon { left: 0; }
  .detail-date p { padding-left: 46px; }
  .detail-date p + p { padding-left: 11px; }
  .detail-time { left: 272px; }
  .detail-time .icon { left: 0; }
  .detail-time p { padding-left: 46px; }
  .detail-time p + p { padding-left: 16px; }
  .detail-venue { left: 458px; }
  .detail-venue .icon { left: 8px; }
  .detail-venue p:first-of-type { padding-left: 50px; }
  .detail-venue p.room { padding-left: 8px; }
  .divider { position: absolute; top: 0; width: 1px; height: 108px; background: var(--orange); }
  .divider-a { left: 255px; }
  .divider-b { left: 441px; }
  .footer-rule { position: absolute; left: 33px; top: 988px; width: 715px; height: 1px; background: var(--rule); }
  .footer-logo { position: absolute; left: 68px; top: 1004px; width: 185px; height: 75px; display: flex; align-items: center; justify-content: center; }
  .contacts { position: absolute; left: 275px; top: 1003px; color: var(--white); font-size: 28px; line-height: 37px; }
  .contacts .row { display: flex; align-items: center; gap: 10px; }
  .contacts svg { flex: none; }
</style>
</head>
<body>
<div class="canvas">
  <div class="flyer">
    <div class="top-band"></div>
    <div class="hero-photo" role="img" aria-label="Photo of three women praying with eyes closed and hands clasped"></div>
    <h1 class="event-title"><span class="line-one">Radiant Harvest</span><span class="line-two">Worship Day</span></h1>
    <div class="logo-box"><span class="org-name">TOLVEX</span></div>

    <div class="retreat-band">
      <p class="headline">A one day prayer retreat.</p>
      <p class="tagline">Jesus Chris is Lord</p>
    </div>

    <div class="keywords">
      <p>Prayer | Sharing the Word</p>
      <p>Panel discussion | Prophecy | Impartation.</p>
    </div>

    <div class="details">
      <div class="detail detail-date">
        <svg class="icon" viewBox="0 0 32 32" aria-hidden="true"><circle cx="16" cy="16" r="16" fill="var(--orange)"/><rect x="8" y="10" width="16" height="14" rx="1.5" fill="none" stroke="#fff" stroke-width="1.8"/><line x1="8" y1="14.5" x2="24" y2="14.5" stroke="#fff" stroke-width="1.8"/><line x1="12" y1="8" x2="12" y2="11.5" stroke="#fff" stroke-width="1.8"/><line x1="20" y1="8" x2="20" y2="11.5" stroke="#fff" stroke-width="1.8"/></svg>
        <p>Tuesday</p>
        <p>July 2nd, 2019</p>
      </div>
      <div class="divider divider-a"></div>
      <div class="detail detail-time">
        <svg class="icon" viewBox="0 0 32 32" aria-hidden="true"><circle cx="16" cy="16" r="16" fill="var(--orange)"/><circle cx="16" cy="16" r="8" fill="none" stroke="#fff" stroke-width="1.8"/><polyline points="16,11 16,16 19.5,18" fill="none" stroke="#fff" stroke-width="1.8"/></svg>
        <p>11:00AM</p>
        <p>to 7:00PM</p>
      </div>
      <div class="divider divider-b"></div>
      <div class="detail detail-venue">
        <svg class="icon" viewBox="0 0 32 32" aria-hidden="true"><circle cx="16" cy="16" r="16" fill="var(--orange)"/><path d="M16 25 C11 19 10 16.5 10 14 a6 6 0 0 1 12 0 c0 2.5 -1 5 -6 11z" fill="none" stroke="#fff" stroke-width="1.8"/><circle cx="16" cy="14" r="2.2" fill="none" stroke="#fff" stroke-width="1.6"/></svg>
        <p>Belmora Hotel,</p>
        <p>4875 Wexley Avenue,</p>
        <p>Portland, Maine 04102</p>
        <p class="room">(Room: Juniper)</p>
      </div>
    </div>

    <div class="footer-rule"></div>
    <div class="footer-logo"><span class="org-name">TOLVEX</span></div>
    <div class="contacts">
      <div class="row">
        <svg width="24" height="24" viewBox="0 0 24 24" aria-hidden="true"><circle cx="12" cy="12" r="10" fill="none" stroke="#fff" stroke-width="1.5"/><ellipse cx="12" cy="12" rx="4.5" ry="10" fill="none" stroke="#fff" stroke-width="1.5"/><line x1="2" y1="12" x2="22" y2="12" stroke="#fff" stroke-width="1.5"/></svg>
        <span>tolvex.org</span>
        <svg width="30" height="24" viewBox="0 0 30 24" aria-hidden="true"><path d="M3 9 q12 -8 24 0 v3 h-6 v-3 h-12 v3 h-6z" fill="none" stroke="#fff" stroke-width="1.5"/><rect x="7" y="13" width="16" height="8" rx="2" fill="none" stroke="#fff" stroke-width="1.5"/></svg>
        <span>207 555 3184</span>
      </div>
      <div class="row">
        <svg width="24" height="20" viewBox="0 0 24 20" aria-hidden="true"><rect x="1.5" y="3" width="21" height="14" fill="none" stroke="#fff" stroke-width="1.5"/><polyline points="1.5,3 12,11 22.5,3" fill="none" stroke="#fff" stroke-width="1.5"/></svg>
        <span>contact@brookhavenfold.org</span>
      </div>
    </div>
  </div>
</div>
</body>
</html>
```